Events Company Needs Website Revamp

Tallwood Expos is an events company that specializes in organizing and marketing large scale consumer and trade events globally.

The new web design should provide easy classification of the events, and allow visitors to find and access the details page within 2 clicks.

There are no strict guidelines on the color theme. It just has to blend naturally with the corporate logo.
Updates

The company logo is uploaded (pdf & ai)

I came across this design which I like very much. Elegant and corporate with nice modern fonttype.

Layout wise, neat and clear. 

Please see how you can emulate the design further. Particularly, highlighting the 2 event arms (Trade/Consumer) clearly.

Target Market(s)

Consumer looking for upcoming events, B2C companies looking to participate, B2B companies looking to connect with other companies

Industry/Entity Type

It Company

Requirements
Must have
• The new design should help to achieve the following objectives:
1) Visitors should be able to easily identify and access the 2 different types of events (i.e. Trade Events and Consumer Events).
2) Visitors should be able to easily find events that interest them (e.g. filter by date, trade or consumer, category [i.e. beauty, retail, F&B, construction, etc.]).
3) Visitors should be able to access an event’s details page within 2 clicks from any page.

Main navigation to include the following links:
- About Us
- Calendar
- Consumer Events
- Trade Events
- Contact Us

Design for Three (3) pages required:
A. Homepage
- Clear differentiation and easy access to the 2 different types of events (trade and consumer)
- Featured area to showcase latest 4-5 events
- Quick way to access events calendar
- Clear call-to-action for newsletter signup
- Social media sharing widgets/buttons
- A section for latest news and press releases
- A section for featured testimonials

B. Events Listing Page
- List of links to all events
- Logos and/or photos of events
- Filter / tags to find events in a specific category (e.g. food, electronics, building & construction, etc.)

C. Events Details Page
- Photo strip to showcase event photos / brochure
- A section with event details (Date, Venue, Event Description, etc.)
- Call-to-action button to visit event website
- Call-to-action button to contact event sales team
- E.g. http://vantly-demo.com/user/brightfoxhk/brightfox-monday-2011 but with the photo strip permanently extended and of a shorter height. Event details and call-to-action buttons should also be easily seen

```html
<!DOCTYPE html>
<html lang="en">
<head>
<meta charset="utf-8">
<title>Tallwood Expos – Consumer Events</title>
<link href="https://fonts.googleapis.com/css2?family=PT+Sans+Narrow:wght@400;700&family=Arimo:wght@400;700&display=swap" rel="stylesheet">
<style>
:root{
  --purple:#6e0f73;
  --purple-dark:#4e0853;
  --purple-light:#8a1e8f;
  --orange:#f07c1e;
  --orange-light:#ffb020;
  --text:#222;
  --muted:#666;
  --rule:#ddd;
  --bar-top:#f2f2f2;
  --bar-bottom:#d6d6d6;
  --white:#fff;
}
*{box-sizing:border-box;margin:0;padding:0}
html,body{width:741px;height:1200px;overflow:hidden;background:var(--white)}
body{position:relative;font-family:"Arimo",Arial,sans-serif;color:var(--text)}
.narrow{font-family:"PT Sans Narrow","Arial Narrow",sans-serif}

/* header */
.site-header{position:absolute;left:0;top:0;width:741px;height:178px}
.site-header svg.band{position:absolute;left:0;top:0}
.logo{position:absolute;left:35px;top:-58px;width:123px;height:123px;border-radius:50%;background:var(--white);border:3px solid var(--purple-light);display:flex;align-items:flex-end;justify-content:center;padding-bottom:30px;gap:5px}
.logo-dot{width:10px;height:10px;border-radius:50%;background:var(--orange)}
.logo-name{font-family:"Arimo",Arial,sans-serif;font-size:12px;color:var(--muted)}
.main-nav{position:absolute;left:262px;top:0;display:flex;height:45px}
.main-nav a{font-family:"PT Sans Narrow","Arial Narrow",sans-serif;color:var(--white);text-decoration:none;font-size:18px;line-height:58px;padding:0 9px;height:45px;border-right:1px solid rgba(255,255,255,.08)}
.main-nav a.current{background:rgba(0,0,0,.14);padding:0 12px}
.sub-nav{position:absolute;left:262px;top:45px;width:242px;height:25px;background:rgba(0,0,0,.12);display:flex;font-size:9px;color:var(--white);align-items:center}
.sub-nav span{flex:1;text-align:center;border-right:1px solid rgba(255,255,255,.08)}

/* filter bar */
.filter-bar{position:absolute;left:33px;top:190px;width:678px;height:48px;background:linear-gradient(var(--bar-top),var(--bar-bottom));display:flex;align-items:center;font-size:10px;color:#333}
.filter-bar .label{width:59px;text-align:center}
.filter-bar .tab{height:48px;line-height:48px;padding:0 15px;border-left:1px solid #c4c4c4}
.filter-bar .tab.active{background:var(--purple);color:var(--white);width:43px;padding:0;text-align:center}
.filter-bar .tab.last{border-right:1px solid #c4c4c4}
.filter-by{margin-left:33px}
.select{margin-left:11px;width:172px;height:20px;background:var(--white);border:1px solid #bbb;font-size:9px;line-height:18px;padding-left:8px;position:relative}
.select::after{content:"";position:absolute;right:0;top:0;width:17px;height:18px;background:var(--purple)}
.select svg{position:absolute;right:4px;top:6px;z-index:1}
.search-btn{margin-left:18px;width:57px;height:19px;border:1px solid #bbb;background:linear-gradient(#fafafa,#e2e2e2);font-size:9px;text-align:center;line-height:17px;font-weight:700;color:#555}

.hatch{position:absolute;left:33px;width:678px;height:7px;background:repeating-linear-gradient(135deg,#e3e3e3 0 2px,transparent 2px 5px)}

h1.section-title{position:absolute;left:33px;top:306px;font-family:"PT Sans Narrow","Arial Narrow",sans-serif;font-size:19px;font-weight:700}

/* event rows */
.event{position:absolute;left:33px;width:678px;height:190px}
.event-logo{position:absolute;left:0;top:0;width:165px;height:117px;border:1px solid #c9a8cc;background:linear-gradient(#fff,#f3f0f3)}
.event-tools{position:absolute;left:0;top:117px;width:165px;height:42px;background:var(--purple-dark);display:flex}
.event-tools span{flex:1;display:flex;align-items:center;justify-content:center;border-right:1px solid rgba(255,255,255,.1)}
.visit{position:absolute;left:0;top:159px;width:165px;height:18px;background:linear-gradient(var(--orange-light),var(--orange));font-size:8px;font-weight:700;color:#4a2a00;line-height:18px;padding-left:17px}
.visit svg{position:absolute;right:7px;top:5px}
.event-body{position:absolute;left:180px;top:0;width:497px}
.event-title{font-family:"PT Sans Narrow","Arial Narrow",sans-serif;color:var(--orange);font-size:17px;font-weight:400;height:21px;border-bottom:1px solid var(--rule);padding-bottom:20px;line-height:14px}
.facts{margin-top:17px;font-size:10px;line-height:15.5px}
.facts b{font-weight:400;color:#111}
.facts span{color:var(--muted)}
.desc{margin-top:17px;font-size:7.6px;line-height:11px;color:var(--muted)}
.desc p+p{margin-top:12px}
.read-more{display:inline-block;margin-top:14px;font-size:8px;color:var(--orange);text-decoration:underline}

/* footer */
.site-footer{position:absolute;left:0;top:1040px;width:741px;height:160px}
.footer-col{position:absolute;top:54px;font-size:9px;color:var(--muted);line-height:12px}
.footer-col h2{font-size:9.5px;color:#111;font-weight:700;margin-bottom:3px}
.social{display:flex;gap:8px;margin-top:7px}
.social i{width:19px;height:19px;border-radius:50%;background:var(--purple-dark);display:block}
.subscribe-form{display:flex;margin-top:11px}
.subscribe-form .field{width:130px;height:16px;border:1px solid #ccc;font-size:8px;font-style:italic;color:#888;padding-left:5px;line-height:14px}
.subscribe-form .submit{width:40px;height:16px;background:linear-gradient(#f4f4f4,#ddd);border:1px solid #ccc;border-left:none;font-size:7px;font-weight:700;color:var(--purple-dark);text-align:center;line-height:14px}
.to-top{position:absolute;left:677px;top:92px;font-size:9px;color:#111;text-align:center;width:22px}
</style>
</head>
<body>

<header class="site-header">
  <svg class="band" width="741" height="178" viewBox="0 0 741 178">
    <defs>
      <radialGradient id="headGlow" cx="0.55" cy="0.35" r="0.7">
        <stop offset="0" stop-color="#84157f"/>
        <stop offset="1" stop-color="#5e0a62"/>
      </radialGradient>
    </defs>
    <rect width="741" height="166" fill="url(#headGlow)"/>
    <path d="M0 166 H741 V170 H0Z" fill="#f07c1e"/>
    <path d="M0 169 Q370 180 741 169 L741 170 Q370 176 0 170Z" fill="#4e0853"/>
  </svg>
  <div class="logo"><i class="logo-dot"></i><span class="logo-name">Tallwood Expos</span></div>
  <nav class="main-nav">
    <a class="current">About Us</a><a>Calendar</a><a>Trade Events</a><a>Consumer Events</a><a>Contact Us</a>
  </nav>
  <div class="sub-nav"><span>Our &nbsp; Story</span><span>History</span><span>Missios</span></div>
</header>

<div class="filter-bar">
  <span class="label">Show:</span>
  <span class="tab active">All</span>
  <span class="tab">Exibitions</span>
  <span class="tab">Events</span>
  <span class="tab last">Roadshows</span>
  <span class="filter-by">FILTER BY</span>
  <div class="select">Food<svg width="9" height="6" viewBox="0 0 9 6"><path d="M0 0H9L4.5 6Z" fill="#fff"/></svg></div>
  <div class="search-btn">Search</div>
</div>

<div class="hatch" style="top:271px"></div>
<h1 class="section-title">Consumer Events</h1>

<!-- event template repeated -->
<article class="event" style="top:349px">
  <div class="event-logo" role="img" aria-label="Veils &amp; Glow event logo"></div>
  <div class="event-tools">
    <span><svg width="16" height="14" viewBox="0 0 16 14"><ellipse cx="8" cy="6" rx="7.5" ry="5.5" fill="#fff"/><path d="M4 10 L3 14 L8 11Z" fill="#fff"/></svg></span>
    <span><svg width="18" height="10" viewBox="0 0 18 10"><rect width="18" height="10" fill="#fff"/><rect x="4" y="2" width="10" height="6" fill="#4e0853"/></svg></span>
    <span><svg width="18" height="14" viewBox="0 0 18 14"><rect x=".5" y=".5" width="17" height="13" fill="none" stroke="#fff"/><path d="M3 11 L7 6 L10 9 L12 7 L15 11Z" fill="#fff"/><circle cx="13" cy="4" r="1.5" fill="#fff"/></svg></span>
    <span><svg width="14" height="16" viewBox="0 0 14 16"><path d="M9 4 L3 10 a2 2 0 0 0 3 3 L12 7 a3.5 3.5 0 0 0 -5 -5 L1.5 7.5" fill="none" stroke="#fff" stroke-width="1.6"/></svg></span>
  </div>
  <div class="visit">Visit Site<svg width="5" height="8" viewBox="0 0 5 8"><path d="M0 0 L5 4 L0 8Z" fill="#4a2a00"/></svg></div>
  <div class="event-body">
    <h2 class="event-title">Veils &amp; Glow</h2>
    <div class="facts">
      <div><b>Venue:</b> <span>Harbourline Convention Centre, Hall 403 - 404</span></div>
      <div><b>Date:</b> <span>14 - 16 August 2009 , Friday - Sunday</span></div>
      <div><b>Time:</b> <span>11am - 9pm</span></div>
      <div>Free Admission</div>
    </div>
    <div class="desc">
      <p>Tying the knot is an exciting time for all couples. And when it comes to planning various aspects of your special day, you'll soon realise that tying up loose ends can be quite exhausting!</p>
      <p>So whether you're scouring for that gorgeous bridal gown, exploring novel ideas, or seeking beauty packages to get you ready for your big day, you'll be inspired at our Veils &amp; Glow Event this August.</p>
    </div>
    <a class="read-more">Read More</a>
  </div>
</article>

<div class="hatch" style="top:560px"></div>

<article class="event" style="top:591px">
  <div class="event-logo" role="img" aria-label="Veils &amp; Glow event logo"></div>
  <div class="event-tools">
    <span><svg width="16" height="14" viewBox="0 0 16 14"><ellipse cx="8" cy="6" rx="7.5" ry="5.5" fill="#fff"/><path d="M4 10 L3 14 L8 11Z" fill="#fff"/></svg></span>
    <span><svg width="18" height="10" viewBox="0 0 18 10"><rect width="18" height="10" fill="#fff"/><rect x="4" y="2" width="10" height="6" fill="#4e0853"/></svg></span>
    <span><svg width="18" height="14" viewBox="0 0 18 14"><rect x=".5" y=".5" width="17" height="13" fill="none" stroke="#fff"/><path d="M3 11 L7 6 L10 9 L12 7 L15 11Z" fill="#fff"/><circle cx="13" cy="4" r="1.5" fill="#fff"/></svg></span>
    <span><svg width="14" height="16" viewBox="0 0 14 16"><path d="M9 4 L3 10 a2 2 0 0 0 3 3 L12 7 a3.5 3.5 0 0 0 -5 -5 L1.5 7.5" fill="none" stroke="#fff" stroke-width="1.6"/></svg></span>
  </div>
  <div class="visit">Visit Site<svg width="5" height="8" viewBox="0 0 5 8"><path d="M0 0 L5 4 L0 8Z" fill="#4a2a00"/></svg></div>
  <div class="event-body">
    <h2 class="event-title">Veils &amp; Glow</h2>
    <div class="facts">
      <div><b>Venue:</b> <span>Harbourline Convention Centre, Hall 403 - 404</span></div>
      <div><b>Date:</b> <span>14 - 16 August 2009 , Friday - Sunday</span></div>
      <div><b>Time:</b> <span>11am - 9pm</span></div>
      <div>Free Admission</div>
    </div>
    <div class="desc">
      <p>Tying the knot is an exciting time for all couples. And when it comes to planning various aspects of your special day, you'll soon realise that tying up loose ends can be quite exhausting!</p>
      <p>So whether you're scouring for that gorgeous bridal gown, exploring novel ideas, or seeking beauty packages to get you ready for your big day, you'll be inspired at our Veils &amp; Glow Event this August.</p>
    </div>
    <a class="read-more">Read More</a>
  </div>
</article>

<div class="hatch" style="top:802px"></div>

<article class="event" style="top:835px">
  <div class="event-logo" role="img" aria-label="Veils &amp; Glow event logo"></div>
  <div class="event-tools">
    <span><svg width="16" height="14" viewBox="0 0 16 14"><ellipse cx="8" cy="6" rx="7.5" ry="5.5" fill="#fff"/><path d="M4 10 L3 14 L8 11Z" fill="#fff"/></svg></span>
    <span><svg width="18" height="10" viewBox="0 0 18 10"><rect width="18" height="10" fill="#fff"/><rect x="4" y="2" width="10" height="6" fill="#4e0853"/></svg></span>
    <span><svg width="18" height="14" viewBox="0 0 18 14"><rect x=".5" y=".5" width="17" height="13" fill="none" stroke="#fff"/><path d="M3 11 L7 6 L10 9 L12 7 L15 11Z" fill="#fff"/><circle cx="13" cy="4" r="1.5" fill="#fff"/></svg></span>
    <span><svg width="14" height="16" viewBox="0 0 14 16"><path d="M9 4 L3 10 a2 2 0 0 0 3 3 L12 7 a3.5 3.5 0 0 0 -5 -5 L1.5 7.5" fill="none" stroke="#fff" stroke-width="1.6"/></svg></span>
  </div>
  <div class="visit">Visit Site<svg width="5" height="8" viewBox="0 0 5 8"><path d="M0 0 L5 4 L0 8Z" fill="#4a2a00"/></svg></div>
  <div class="event-body">
    <h2 class="event-title">Veils &amp; Glow</h2>
    <div class="facts">
      <div><b>Venue:</b> <span>Harbourline Convention Centre, Hall 403 - 404</span></div>
      <div><b>Date:</b> <span>14 - 16 August 2009 , Friday - Sunday</span></div>
      <div><b>Time:</b> <span>11am - 9pm</span></div>
      <div>Free Admission</div>
    </div>
    <div class="desc">
      <p>Tying the knot is an exciting time for all couples. And when it comes to planning various aspects of your special day, you'll soon realise that tying up loose ends can be quite exhausting!</p>
      <p>So whether you're scouring for that gorgeous bridal gown, exploring novel ideas, or seeking beauty packages to get you ready for your big day, you'll be inspired at our Veils &amp; Glow Event this August.</p>
    </div>
    <a class="read-more">Read More</a>
  </div>
</article>

<footer class="site-footer">
  <svg width="741" height="20" viewBox="0 0 741 20" style="position:absolute;left:0;top:0">
    <path d="M60 13 Q370 4 680 13Z" fill="#4e0853"/>
    <rect y="13" width="741" height="2" fill="#f07c1e"/>
  </svg>
  <div class="footer-col" style="left:34px">
    <h2>Copyright</h2>
    <div>© Tallwood Expos 2009-2010. All Rights Reserved.</div>
    <div style="margin-top:15px">• Tel: (65) 6100-2830 or (65) 6100-2831</div>
    <div>• Fax: (65) 6100-2840</div>
    <div>• hello@tallwoodexpos.test</div>
  </div>
  <div class="footer-col" style="left:330px">
    <h2>Connect wit Us</h2>
    <div class="social"><i></i><i></i><i></i><i></i></div>
  </div>
  <div class="footer-col" style="left:468px">
    <h2>Subscribe</h2>
    <div>Get free event updates &amp; specials!</div>
    <div class="subscribe-form"><div class="field">Enter Email</div><div class="submit">SUBMIT</div></div>
  </div>
  <div class="to-top">
    <svg width="20" height="33" viewBox="0 0 20 33"><path d="M10 0 L20 12 L15 12 L15 33 L10 29 L5 33 L5 12 L0 12Z" fill="#f07c1e"/></svg>
    <div>Top</div>
  </div>
</footer>

</body>
</html>
```